Marcus Delbridge Finance

Need a personal website advertising Equipment Finance,Business Finance,Commercial Finance, Construction Finance, Bridging Finance. Similar websites are www.corvalend.com.au / www.tarmivest.com.au / www.qbr7.com.au /wwwhalvecredit.com.au

Target Market(s)

Business People

Industry/Entity Type

Business

Number of Pages Required

3 page

Font styles to use
Serif
Sans Serif

Requirements
Must have
• All i want is a simple corporate looking website advertising Equipment Finance, Commercial Finance, Construction Finance, Business Finance, Bridging Finance,

```html
<!DOCTYPE html>
<html lang="en">
<head>
<meta charset="utf-8">
<title>Marcus Delbridge Finance</title>
<link href="https://fonts.googleapis.com/css2?family=Open+Sans:wght@600;700&family=Lato:wght@400;700&display=swap" rel="stylesheet">
<style>
:root{
  --blue:#2f5fad;
  --blue-dark:#1f3e7a;
  --ink:#111;
  --header-bg:#f5f5f5;
  --panel:#ebebeb;
  --footer:#000;
  --line:#d6d6d6;
}
*{margin:0;padding:0;box-sizing:border-box}
html,body{width:884px;height:1200px;overflow:hidden}
body{position:relative;background:#fff;font-family:'Lato',sans-serif;color:var(--ink)}
.abs{position:absolute}
.heading{font-family:'Open Sans',sans-serif;font-weight:700}

.site-header{left:0;top:0;width:884px;height:70px;background:var(--header-bg)}
.brand{left:73px;top:22px;display:flex;align-items:center;gap:8px}
.brand-square{width:20px;height:20px;background:var(--blue)}
.brand-name{font-family:'Open Sans',sans-serif;font-weight:600;font-size:19px;color:var(--blue-dark)}
.main-nav{left:407px;top:33px;display:flex;gap:25px;font-family:'Open Sans',sans-serif;font-weight:600;font-size:10.5px;letter-spacing:.2px}
.main-nav a{color:#222;text-decoration:none}
.main-nav a.active{color:var(--blue);position:relative}
.main-nav a.active::after{content:"";position:absolute;left:0;right:0;top:34px;height:3px;background:var(--blue)}
.call{left:700px;top:20px;display:flex;align-items:center;gap:8px}
.call-divider{width:1px;height:30px;background:#999}
.call-text{font-family:'Open Sans',sans-serif;font-weight:700;font-size:10.5px;line-height:15px}
.call-text span{display:block;color:var(--blue);font-weight:600}

.hero{left:0;top:70px;width:884px;height:380px;background:linear-gradient(180deg,#3d7fd0 0%,#2a5d9e 45%,#1c2f4d 100%)}
.hero-box{left:234px;top:198px;width:415px;height:139px;background:rgba(25,45,65,.82);text-align:center;color:#fff}
.hero-box h1{font-size:27px;margin-top:28px}
.hero-box p{font-size:11.5px;line-height:15px;margin:10px auto 0;width:320px}
.hero-btn{left:390px;top:324px;width:104px;height:26px;background:var(--blue);color:#fff;font-size:11.5px;display:flex;align-items:center;justify-content:center}
.hero-dots{left:422px;top:390px;display:flex;gap:5px}
.hero-dots i{width:9px;height:9px;border:1px solid #fff}
.hero-dots i.on{background:#fff}

.welcome h2{font-size:22px;letter-spacing:.3px}
.welcome h2 span{color:var(--blue)}
.rule{height:2px;background:var(--blue)}
.welcome p{font-size:10.3px;line-height:16.2px;width:510px}
.btn{background:var(--blue);color:#fff;font-size:11px;font-weight:700;display:flex;align-items:center;justify-content:center}

.inquiry{left:611px;top:486px;width:202px;height:208px;background:var(--panel);box-shadow:0 8px 6px -6px rgba(0,0,0,.45)}
.inquiry h3{text-align:center;font-size:16px;margin-top:12px}
.inquiry h3 span{color:var(--blue)}
.field{left:13px;width:176px;background:#fff;border:1px solid var(--line);font-size:8.5px;color:#666;padding:9px 8px}

.services-band{left:0;top:726px;width:884px;height:136px;background:linear-gradient(120deg,#1d4fa8 0%,#1a5ab8 45%,#1f6fb0 70%,#14868f 100%)}
.services-title{left:0;top:745px;width:884px;text-align:center;color:#fff;font-size:22px}
.services-rule{left:418px;top:788px;width:48px;height:2px;background:#9fb3d4}
.service-box{width:77px;height:77px;background:#fff;border:2px solid var(--blue);display:flex;align-items:center;justify-content:center}
.service-box div{width:40px;height:40px;background:#222;border-radius:3px}
.service-label{width:160px;text-align:center;font-size:13px;font-weight:700;color:#111}

.footer{left:0;top:967px;width:884px;height:201px;background:var(--footer);color:#fff}
.footer h4{font-family:'Open Sans',sans-serif;font-size:11.5px;font-weight:700;letter-spacing:.3px}
.footer h4 span{color:var(--blue)}
.frule{width:25px;height:2px;background:var(--blue)}
.links{list-style:none;font-size:9.5px;line-height:24px}
.links li::before{content:"•";margin-right:5px}
.links li.active{color:var(--blue)}
.contact{font-size:9.8px;line-height:13.5px}
.contact .row{display:flex;gap:8px;margin-bottom:8px}
.contact svg{flex:none;margin-top:2px}
.map{left:461px;top:1038px;width:180px;height:92px;border:2px solid #888;background:linear-gradient(135deg,#e8e6df,#d9d6cb)}
.footer-mark{left:729px;top:1036px;width:62px;height:62px;background:#9a9a9a}
.social{left:713px;top:1114px;display:flex;gap:6px}
.social i{width:19px;height:19px;background:var(--blue)}
.copyright{left:0;top:1168px;width:884px;height:32px;background:var(--blue);color:#fff;font-size:10px;display:flex;align-items:center;justify-content:center}
</style>
</head>
<body>

<header class="abs site-header">
  <div class="abs brand"><div class="brand-square"></div><div class="brand-name">Marcus Delbridge Finance</div></div>
  <nav class="abs main-nav">
    <a class="active">HOME</a><a>ABOUT US</a><a>SERVICES</a><a>CONTACT US</a>
  </nav>
  <div class="abs call">
    <svg width="24" height="24" viewBox="0 0 24 24"><path d="M6 3l3 4-2 2c1 3 3 5 6 6l2-2 4 3-2 3C10 19 5 14 3 6z" fill="#2f5fad"/></svg>
    <div class="call-divider"></div>
    <div class="call-text"><span>CALL US</span>(555)-218-4630</div>
  </div>
</header>

<section class="abs hero" role="img" aria-label="Photo looking up at glass office towers against a blue sky"></section>
<div class="abs hero-box">
  <h1 class="heading">Construction Finance</h1>
  <p>Lorem ipsum dolor sit amet, consectetuer adipiscing elit, sed diam nonummy nib adipiscing elit, ed diam nonummy nibh euis</p>
</div>
<div class="abs hero-btn">CALL US TODAY</div>
<div class="abs hero-dots"><i class="on"></i><i></i><i></i></div>

<section class="welcome">
  <h2 class="abs heading" style="left:73px;top:496px">WELCOME TO <span>MARCUS DELBRIDGE</span> FINANCE</h2>
  <div class="abs rule" style="left:73px;top:536px;width:48px"></div>
  <p class="abs" style="left:74px;top:557px">Lorem ipsum dolor sit amet, consectetuer adipiscing elit, sed diam nonummy nibh euismod tincidunt ut laoreet dolore magna aliquam erat volutpat. Ut wisi enim ad minim veniam, quis nostrud exerci tation ullamcorper suscipit lobortis nisl ut aliquip ex ea commodo consequat. Duis autem vel eum iriure dolor in hendrerit in vulputate velit esse molestie consequat, vel illum dolore eu feugiat nulla facilisis at vero eros et accumsan et iusto odio dignissim qui blandit praesent luptatum zzril delenit augue duis dolore te feugait nulla facilisi.</p>
  <div class="abs btn" style="left:73px;top:657px;width:89px;height:27px">READ MORE</div>
</section>

<aside class="abs inquiry">
  <h3 class="heading">QUICK <span>INQUIRY</span></h3>
  <div class="abs field" style="top:42px;height:28px">Name</div>
  <div class="abs field" style="top:75px;height:28px">Email</div>
  <div class="abs field" style="top:108px;height:52px">Message</div>
  <div class="abs btn" style="left:13px;top:169px;width:176px;height:28px;font-size:12px">SUBMIT</div>
</aside>

<section>
  <div class="abs services-band" role="img" aria-label="Blue low-poly geometric background"></div>
  <h2 class="abs heading services-title">OUR SERVICES</h2>
  <div class="abs services-rule"></div>

  <div class="abs service-box" style="left:90px;top:820px"><div role="img" aria-label="Excavator icon"></div></div>
  <div class="abs service-label" style="left:48px;top:908px">Equipment Finance</div>
  <div class="abs service-box" style="left:246px;top:820px"><div role="img" aria-label="Hand holding cash icon"></div></div>
  <div class="abs service-label" style="left:204px;top:908px">Business Finance</div>
  <div class="abs service-box" style="left:405px;top:820px"><div role="img" aria-label="Office building icon"></div></div>
  <div class="abs service-label" style="left:363px;top:908px">Commercial Finance</div>
  <div class="abs service-box" style="left:560px;top:820px"><div role="img" aria-label="Crane and building icon"></div></div>
  <div class="abs service-label" style="left:518px;top:908px">Construction Finance</div>
  <div class="abs service-box" style="left:716px;top:820px"><div role="img" aria-label="Bridge icon"></div></div>
  <div class="abs service-label" style="left:674px;top:908px">Bridging Finance</div>
</section>

<footer class="abs footer">
  <h4 class="abs" style="left:73px;top:32px">QUICK <span>LINKS</span></h4>
  <div class="abs frule" style="left:73px;top:54px"></div>
  <ul class="abs links" style="left:73px;top:62px">
    <li class="active">HOME</li><li>ABOUT US</li><li>SERVICES</li><li>CONTACT US</li>
  </ul>

  <h4 class="abs" style="left:230px;top:32px">CONTACT <span>DETAILS</span></h4>
  <div class="abs frule" style="left:230px;top:54px"></div>
  <div class="abs contact" style="left:230px;top:67px;width:170px">
    <div class="row"><svg width="9" height="12" viewBox="0 0 9 12"><path d="M4.5 0a4.5 4.5 0 0 0-4.5 4.5C0 8 4.5 12 4.5 12S9 8 9 4.5A4.5 4.5 0 0 0 4.5 0zm0 6.3a1.8 1.8 0 1 1 0-3.6 1.8 1.8 0 0 1 0 3.6z" fill="#2f5fad"/></svg><div><b style="font-weight:700">Marcus Delbridge Finance</b><br>Sed ut perspiciatis unde omnis iste natus errorluptatem</div></div>
    <div class="row"><svg width="10" height="10" viewBox="0 0 24 24"><path d="M6 3l3 4-2 2c1 3 3 5 6 6l2-2 4 3-2 3C10 19 5 14 3 6z" fill="#2f5fad"/></svg><div>0155 218 463</div></div>
    <div class="row"><svg width="10" height="8" viewBox="0 0 10 8"><rect width="10" height="8" fill="#2f5fad"/><path d="M0 0l5 4 5-4" stroke="#000" fill="none"/></svg><div>info@delbridgefinance.com</div></div>
  </div>

  <h4 class="abs" style="left:458px;top:32px">LOCATION <span>MAP</span></h4>
  <div class="abs frule" style="left:458px;top:54px"></div>
</footer>
<div class="abs map" role="img" aria-label="Street map of the office location"></div>
<div class="abs footer-mark"></div>
<div class="abs social"><i></i><i></i><i></i><i></i></div>
<div class="abs copyright">Copyright © 2017 Marcus Delbridge Finance. All Rights Reserved</div>

</body>
</html>
```